Card Design for my dog training business Brightpaw Obedience

Need a business card design for my dog training business with my new logo. Want the card to come off professional yet fun. Want it to be very eye catchy as well. I normally have these at vet clinics, pet stores, and groomers. so need it to look better than my competitors.
Target Market(s)
dog owners
Industry/Entity Type
Dog Training
Contact Information for Business Card
needs logo, my name and info
Font styles to use
Serif
Colors
0255a3
ffffff
ec1f27
000000
333333
fbfbfb
Requirements
Must have
- Brightpaw Obedience
- Felix Orland
- 415 903 2276
- info@brightpawobedience.example
- www.brightpawobedience.example

```html
<!DOCTYPE html>
<html lang="en">
<head>
<meta charset="utf-8">
<title>Brightpaw Obedience – Business Card</title>
<link rel="stylesheet" href="https://fonts.googleapis.com/css2?family=Cinzel:wght@400&family=EB+Garamond:ital@1&family=Roboto:wght@300&display=swap">
<style>
  :root {
    --page-bg: #ececec;
    --card-bg: #1b1b1c;
    --card-bg-deep: #0e0e0f;
    --silver: #c9c9c9;
    --silver-soft: #b3b3b3;
  }
  * { margin: 0; padding: 0; box-sizing: border-box; }
  html, body {
    width: 1125px;
    height: 1200px;
    overflow: hidden;
    background: var(--page-bg);
  }
  .canvas {
    position: relative;
    width: 1125px;
    height: 1200px;
  }
  .card {
    position: absolute;
    left: 150px;
    width: 826px;
    height: 471px;
    background: var(--card-bg);
  }
  .card--front { top: 98px; }
  .card--back {
    top: 631px;
    background: linear-gradient(160deg, var(--card-bg) 40%, var(--card-bg-deep) 100%);
  }

  /* Front */
  .brand-name {
    font-family: "Cinzel", serif;
    font-weight: 400;
    color: var(--silver);
    text-align: center;
    letter-spacing: 2px;
  }
  .card--front .brand-name {
    position: absolute;
    left: 60px;
    top: 190px;
    width: 260px;
    font-size: 28px;
    line-height: 40px;
  }
  .divider {
    position: absolute;
    left: 336px;
    top: 152px;
    width: 2px;
    height: 177px;
    background: var(--silver-soft);
  }
  .contact-block {
    position: absolute;
    left: 387px;
    top: 146px;
  }
  .person-name {
    font-family: "Cinzel", serif;
    font-weight: 400;
    font-size: 30px;
    letter-spacing: 1.5px;
    color: var(--silver);
    line-height: 36px;
  }
  .contact-list {
    list-style: none;
    margin-top: 16px;
  }
  .contact-list li {
    display: flex;
    align-items: center;
    height: 26.5px;
    font-family: "Roboto", sans-serif;
    font-weight: 300;
    font-size: 19px;
    color: var(--silver);
  }
  .contact-list svg {
    width: 17px;
    height: 17px;
    margin-right: 13px;
    flex: none;
    fill: var(--silver);
  }
  .tagline {
    margin-top: 18px;
    font-family: "EB Garamond", serif;
    font-style: italic;
    font-size: 19px;
    color: var(--silver);
  }

  /* Back */
  .card--back .brand-name {
    position: absolute;
    left: 0;
    top: 180px;
    width: 826px;
    font-size: 38px;
    line-height: 52px;
  }
</style>
</head>
<body>
<main class="canvas">
  <section class="card card--front">
    <p class="brand-name">Brightpaw<br>Obedience</p>
    <div class="divider"></div>
    <div class="contact-block">
      <h1 class="person-name">FELIX ORLAND</h1>
      <ul class="contact-list">
        <li>
          <svg viewBox="0 0 24 24" aria-hidden="true"><path d="M6.6 10.8c1.4 2.8 3.8 5.1 6.6 6.6l2.2-2.2c.3-.3.7-.4 1-.2 1.1.4 2.3.6 3.6.6.6 0 1 .4 1 1V20c0 .6-.4 1-1 1C10.6 21 3 13.4 3 4c0-.6.4-1 1-1h3.5c.6 0 1 .4 1 1 0 1.3.2 2.5.6 3.6.1.3 0 .7-.2 1z"/></svg>
          415 903 2276
        </li>
        <li>
          <svg viewBox="0 0 24 24" aria-hidden="true"><path d="M3 6h18v12H3z M3 6l9 7 9-7" fill="none" stroke="currentColor"/><path d="M3 6h18v1.5l-9 6.5-9-6.5zM3 9.5l9 6.5 9-6.5V18H3z"/></svg>
          info@brightpawobedience.example
        </li>
        <li>
          <svg viewBox="0 0 24 24" aria-hidden="true"><circle cx="12" cy="12" r="9" fill="none" stroke="#c9c9c9" stroke-width="2.5"/><path d="M8 7c2 0 3 2 2 3s-3 1-2 3 2 2 1 4c-2-1-4-3-4-6 0-2 1-3 3-4zM14 12c2 0 3 1 3 3-1 1-2 2-3 2-1-2-2-4 0-5z"/></svg>
          brightpawobedience.example
        </li>
      </ul>
      <p class="tagline">“Training dogs across Texas one dog at a time.”</p>
    </div>
  </section>

  <section class="card card--back">
    <p class="brand-name">Brightpaw<br>Obedience</p>
  </section>
</main>
</body>
</html>
```